Mara Penrith Copywriter Website

I am starting a new business as a freelance copywriter. Trying to set up the website for my business is proving to be too technical for me. I would like a simple, clean website using primarily black and white. I have attached the logo I would like used. I would like the menu icons to be Home, Services, Portfolio, Blog, Contact. I would like my mobile phone number (0412 583 906) and email address (mara.penrith.copywriter@fernmail.test) used in the header of the site. I need the site to be easily manageable and inter-changeable for me to be able to move things around and add images, etc with ease.

I would like the home page to be a static page with space for an image of myself somewhere (I haven't had this taken as yet), an area to put a bit about myself and my business, and also somewhere to include social media icons/links. Again, I would like the whole website and home page to be easily managed so that I can add/delete things with ease.

I would like the image of the typewriter used in the website somewhere also please.

Coding

Coded - Design and coding required

Number of Pages Required

5+ page

Font styles to use
Sans Serif
Script

Colors
fdf0f6

Requirements
Must have
• The logo provided
• Ability to change page contents easily
• Ability to add social media icons as needed
Nice to have
• Use of the typewriter image
Should not have
• Complicated pages that are not easily editable

```html
<!DOCTYPE html>
<html lang="en">
<head>
<meta charset="utf-8">
<title>Mara Penrith Copywriter</title>
<link href="https://fonts.googleapis.com/css2?family=Great+Vibes&family=Montserrat:wght@400;600;700&family=Open+Sans:wght@400;600&display=swap" rel="stylesheet">
<style>
  :root {
    --pink: #f7e4e8;
    --pink-soft: #fdf0f6;
    --accent: #d98ea0;
    --ink: #1c1c1c;
    --text: #555555;
    --muted: #8a8a8a;
    --line: #e6e6e6;
    --white: #ffffff;
  }
  * { box-sizing: border-box; margin: 0; padding: 0; }
  html, body { width: 678px; height: 1200px; overflow: hidden; background: var(--white); }
  body { font-family: "Open Sans", Arial, sans-serif; color: var(--text); position: relative; }
  .script { font-family: "Great Vibes", cursive; font-weight: 400; color: var(--ink); }

  /* Header */
  .site-header { position: absolute; top: 0; left: 0; width: 678px; height: 76px; background: var(--white); }
  .brand { position: absolute; left: 30px; top: 28px; display: flex; align-items: center; gap: 8px; }
  .brand-mark { width: 10px; height: 10px; border-radius: 50%; background: var(--accent); }
  .brand-name { font-family: "Montserrat", sans-serif; font-size: 12px; font-weight: 600; letter-spacing: 1.2px; color: var(--ink); white-space: nowrap; }
  .contact-bar { position: absolute; right: 28px; top: 12px; display: flex; gap: 16px; font-size: 9.5px; color: var(--muted); }
  .contact-bar span { display: flex; align-items: center; gap: 5px; }
  .main-nav { position: absolute; right: 28px; top: 42px; display: flex; gap: 20px; align-items: center; font-family: "Montserrat", sans-serif; font-size: 9.5px; font-weight: 600; letter-spacing: .5px; color: var(--ink); }
  .main-nav .active { color: var(--accent); }

  /* Hero */
  .hero { position: absolute; top: 76px; left: 0; width: 678px; height: 292px; display: flex; }
  .hero-photo { width: 339px; height: 292px; background: radial-gradient(ellipse at 50% 50%, #3a3a3a 0%, #6e6e6e 30%, #e9e9e9 58%, #f6f6f6 100%); }
  .hero-panel { width: 339px; height: 292px; background: var(--pink); padding: 52px 36px 0 40px; }
  .hero-title { font-size: 46px; line-height: 1; margin-bottom: 18px; }
  .hero-text { font-size: 9.5px; line-height: 1.65; color: var(--text); margin-bottom: 26px; }
  .btn { display: inline-block; background: var(--ink); color: var(--white); font-family: "Montserrat", sans-serif; font-size: 9px; font-weight: 600; letter-spacing: .8px; padding: 10px 16px; }

  /* About */
  .about { position: absolute; top: 368px; left: 0; width: 678px; height: 300px; }
  .section-title { font-size: 40px; text-align: center; position: absolute; top: 42px; left: 0; width: 678px; line-height: 1; }
  .about .rule { position: absolute; top: 94px; left: 309px; width: 60px; height: 1px; background: var(--line); }
  .portrait-ring { position: absolute; left: 52px; top: 122px; width: 168px; height: 168px; border-radius: 50%; border: 1px solid var(--line); display: flex; align-items: center; justify-content: center; }
  .portrait { width: 150px; height: 150px; border-radius: 50%; background: radial-gradient(circle at 50% 40%, #e8cdb8 0%, #c9a27f 45%, #e9e9e9 80%); }
  .about-copy { position: absolute; left: 270px; top: 162px; width: 360px; }
  .about-heading { font-family: "Montserrat", sans-serif; font-size: 15px; font-weight: 700; color: var(--ink); letter-spacing: .4px; margin-bottom: 14px; }
  .about-text { font-size: 9.5px; line-height: 1.7; }

  /* Services */
  .services { position: absolute; top: 690px; left: 0; width: 678px; height: 330px; }
  .services-photo { position: absolute; inset: 0; background: linear-gradient(90deg, #ffffff 0%, #fbf9f7 35%, #e8ddd3 60%, #c9b6a6 80%, #9e8e82 100%); }
  .services-title { position: absolute; left: 52px; top: 40px; font-size: 40px; line-height: 1; }
  .services-text { position: absolute; left: 52px; top: 94px; width: 300px; font-size: 9.5px; line-height: 1.65; }
  .service-list { position: absolute; left: 52px; top: 150px; display: grid; grid-template-columns: 140px 140px; row-gap: 9px; list-style: none; font-size: 9.5px; color: var(--ink); }
  .service-list li { display: flex; align-items: center; gap: 8px; }
  .service-list li::before { content: ""; width: 6px; height: 6px; border-radius: 50%; background: var(--accent); }
  .services .btn { position: absolute; left: 52px; top: 266px; }

  /* Footer */
  .site-footer { position: absolute; top: 1020px; left: 0; width: 678px; height: 180px; background: var(--white); text-align: center; }
  .social { display: flex; justify-content: center; gap: 12px; margin-top: 40px; }
  .social span { width: 28px; height: 28px; border-radius: 50%; border: 1px solid var(--accent); display: block; }
  .footer-nav { margin-top: 20px; font-size: 9px; color: var(--text); display: flex; justify-content: center; gap: 12px; }
  .footer-nav i { font-style: normal; color: var(--line); }
  .copyright { margin-top: 14px; font-size: 8.5px; color: var(--muted); }
</style>
</head>
<body>
  <header class="site-header">
    <div class="brand"><span class="brand-mark"></span><span class="brand-name">MARA PENRITH COPYWRITER</span></div>
    <div class="contact-bar">
      <span><svg width="9" height="9" viewBox="0 0 24 24"><path d="M6.6 10.8a15 15 0 0 0 6.6 6.6l2.2-2.2a1 1 0 0 1 1-.3 11 11 0 0 0 3.6.6 1 1 0 0 1 1 1V20a1 1 0 0 1-1 1A17 17 0 0 1 3 4a1 1 0 0 1 1-1h3.5a1 1 0 0 1 1 1c0 1.3.2 2.5.6 3.6a1 1 0 0 1-.3 1z" fill="#d98ea0"/></svg>0412 583 906</span>
      <span><svg width="10" height="8" viewBox="0 0 20 16"><rect x="1" y="1" width="18" height="14" fill="none" stroke="#d98ea0" stroke-width="2"/><path d="M1 1l9 7 9-7" fill="none" stroke="#d98ea0" stroke-width="2"/></svg>mara.penrith.copywriter@fernmail.test</span>
    </div>
    <nav class="main-nav">
      <span class="active">HOME</span><span>SERVICES</span><span>PORTFOLIO</span><span>BLOG</span><span>CONTACT</span>
      <svg width="10" height="10" viewBox="0 0 20 20"><circle cx="8" cy="8" r="6" fill="none" stroke="#1c1c1c" stroke-width="2.5"/><path d="M12.5 12.5L18 18" stroke="#1c1c1c" stroke-width="2.5"/></svg>
    </nav>
  </header>

  <section class="hero">
    <div class="hero-photo" role="img" aria-label="Vintage black typewriter with a sheet of paper on a white desk"></div>
    <div class="hero-panel">
      <h1 class="hero-title script">mara penrith</h1>
      <p class="hero-text">Ut enim ad minima veniam, quis nostrum exercitationem ullam corporis suscipit laboriosam, nisi ut aliquid ex ea commodi consequatur vel eum iure reprehenderit.</p>
      <span class="btn">GET MORE INFO</span>
    </div>
  </section>

  <section class="about">
    <h2 class="section-title script">About Me</h2>
    <div class="rule"></div>
    <div class="portrait-ring"><div class="portrait" role="img" aria-label="Portrait photo of the copywriter"></div></div>
    <div class="about-copy">
      <h3 class="about-heading">I'M A FREELANCE COPYWRITER</h3>
      <p class="about-text">Nemo enim ipsam voluptatem quia voluptas sit aspernatur aut odit aut fugit, sed quia consequuntur magni dolores eos qui ratione voluptatem sequi nesciunt. Neque porro quisquam est, qui dolorem ipsum quia dolor sit amet, consectetur, adipisci velit, sed quia non numquam eius modi tempora incidunt ut labore et dolore magnam aliquam quaerat voluptatem.</p>
    </div>
  </section>

  <section class="services">
    <div class="services-photo" role="img" aria-label="Hands typing on a laptop keyboard, softly faded to white on the left"></div>
    <h2 class="services-title script">Services</h2>
    <p class="services-text">Duis aute irure dolor in reprehenderit in voluptate velit esse cillum dolore eu fugiat nulla pariatur, excepteur sint occaecat cupidatat non proident.</p>
    <ul class="service-list">
      <li>Website Copywriter</li><li>Articles</li>
      <li>SEO Copywriter</li><li>Leaflets &amp; Brochures</li>
      <li>Newsletters</li><li>Product Descriptions</li>
      <li>Press Releases</li><li>Blog Writing</li>
      <li>Case Studies</li>
    </ul>
    <span class="btn">READ MORE</span>
  </section>

  <footer class="site-footer">
    <div class="social"><span></span><span></span><span></span><span></span></div>
    <div class="footer-nav"><span>Home</span><i>|</i><span>Services</span><i>|</i><span>Portfolio</span><i>|</i><span>Blog</span><i>|</i><span>Contact</span></div>
    <p class="copyright">Mara Penrith © 2016 All rights reserved.</p>
  </footer>
</body>
</html>
```